Corporate web site design for a blockchain oriented company

Design a web site for Velmora. The company works on blockchain projects, mostly in B2B . Logo and content of the web site are attached with the project.

Corporate web sites means that we need to present the company and, at least, two of its projects.

Target Market(s)

B2B (Telecom, Gvt, online e-commerce web sites, banks, insurance ...)

Number of Pages Required

3 page

Font styles to use
Sans Serif

Requirements
Must have
• Landing page
• Page for KYC product
• Page for Loyalty product
• Team presentation
• Contact form
• Company presentation
• Several section can be in one page.
Nice to have
• Teaser video per project.
Should not have
• Heavy web site with a lot of animations.

```html
<!DOCTYPE html>
<html lang="en">
<head>
<meta charset="utf-8">
<title>Velmora — Blockchain solutions provider</title>
<link href="https://fonts.googleapis.com/css2?family=Roboto+Condensed:wght@400;700&family=Open+Sans:wght@400;600;700&display=swap" rel="stylesheet">
<style>
:root{
  --purple:#5a2a8e;
  --purple-deep:#3a1770;
  --red:#d3163b;
  --red-deep:#b80f31;
  --ink:#111;
  --text:#444;
  --grey-band:#ececec;
  --disc:#dcdcdc;
  --white:#fff;
}
*{margin:0;padding:0;box-sizing:border-box}
html,body{width:1200px;height:3782px;overflow:hidden;background:var(--white)}
body{position:relative;font-family:"Open Sans",sans-serif;color:var(--text)}
.abs{position:absolute}

/* nav */
.brand{font-family:"Roboto Condensed",sans-serif;font-weight:700;font-size:34px;letter-spacing:4px;color:var(--ink);display:flex;align-items:center;gap:12px}
.brand .dot{width:22px;height:22px;border-radius:50%;background:var(--ink)}
.nav-link{top:51px;font-family:"Roboto Condensed",sans-serif;font-size:14px;color:var(--ink);white-space:nowrap}
.nav-link.active{color:var(--purple)}
.login{left:960px;top:44px;width:82px;height:34px;border-radius:17px;background:var(--red);color:#fff;font-family:"Roboto Condensed",sans-serif;font-weight:700;font-size:14px;display:flex;align-items:center;justify-content:center}

/* hero */
.hero-title{left:160px;top:180px;font-family:"Roboto Condensed",sans-serif;font-weight:400;font-size:64px;line-height:74px;color:var(--ink)}
.hero-title span{color:var(--purple)}
.ticks{left:160px;top:338px;list-style:none;font-family:"Roboto Condensed",sans-serif;font-size:21px;color:var(--ink)}
.ticks li{display:flex;align-items:center;gap:10px;margin-bottom:12px}
.ticks svg{width:20px;height:20px}
.btn{display:flex;align-items:center;justify-content:center;border-radius:24px;color:#fff;font-family:"Roboto Condensed",sans-serif}
.hero-btn{left:160px;top:438px;width:148px;height:44px;background:var(--purple);font-size:21px}
.emblem{left:650px;top:150px;width:400px;height:350px;display:flex;align-items:center;justify-content:center;gap:18px}
.emblem .mark{width:70px;height:70px;border-radius:50%;background:var(--ink)}
.emblem .name{font-family:"Roboto Condensed",sans-serif;font-weight:700;font-size:64px;color:var(--ink)}

/* why */
.why-title{left:0;width:1200px;top:700px;text-align:center;color:#fff;font-family:"Roboto Condensed",sans-serif;font-weight:400;font-size:42px}
.why-text{left:285px;width:630px;top:768px;text-align:center;color:#fff;font-size:14.5px;line-height:25px}
.video{left:257px;top:902px;width:686px;height:396px;background:linear-gradient(135deg,#2a3550,#6f7f99 45%,#1d1c2e);box-shadow:0 18px 24px rgba(0,0,0,.3);border:3px solid #fff}
.play{left:576px;top:1074px;width:50px;height:50px;border-radius:50%;background:var(--red)}

/* products */
.section-title{left:0;width:1200px;text-align:center;font-family:"Roboto Condensed",sans-serif;font-weight:400;font-size:42px}
.prod-h{font-family:"Roboto Condensed",sans-serif;font-weight:400;font-size:36px;color:var(--ink)}
.prod-p{font-size:14.5px;line-height:27.5px;text-align:justify;width:445px}
.disc{border-radius:50%;background:var(--disc)}
.ring{border-radius:50%;border:2px solid var(--red)}
.art{border-radius:6px}

/* blog */
.card-img{width:272px;height:152px}
.date{height:20px;display:flex;font-size:11px;color:#fff}
.date b{background:var(--red);padding:2px 12px;font-weight:400}
.date i{background:#111;width:28px}
.card-t{font-weight:700;font-size:15px;color:var(--ink);width:272px}
.card-p{font-size:12px;line-height:17px;width:272px;color:#555}
.card-more{font-size:12px;color:var(--purple)}

/* join */
.join-h{left:0;width:1200px;top:3062px;text-align:center;color:#fff;font-family:"Roboto Condensed",sans-serif;font-weight:400;font-size:40px}
.join-p{left:0;width:1200px;top:3133px;text-align:center;color:#fff;font-family:"Roboto Condensed",sans-serif;font-size:28px;line-height:38px}
.join-btn{left:494px;top:3252px;width:214px;height:48px;background:var(--red);font-size:24px;font-weight:700}

/* footer */
.f-h{font-family:"Roboto Condensed",sans-serif;font-size:21px;color:var(--ink);letter-spacing:.5px}
.f-list{list-style:none;font-size:14px;color:var(--ink)}
.f-list li{margin-bottom:11px;display:flex;align-items:center;gap:8px}
.f-list li::before{content:"";border-left:6px solid var(--red);border-top:5px solid transparent;border-bottom:5px solid transparent}
.social{left:170px;top:3578px;display:flex;gap:18px}
.social span{width:32px;height:32px;border-radius:50%;background:#111}
.social span.r{background:var(--red)}
.contact-item{font-size:12px;color:#333;line-height:17px}
.contact-item b{display:block;font-size:14px;font-weight:600;color:var(--ink);text-transform:uppercase}
.copy{left:462px;top:3708px;font-size:13px;color:#333}
</style>
</head>
<body>

<!-- backgrounds -->
<svg class="abs" style="left:0;top:0" width="1200" height="3782" viewBox="0 0 1200 3782" aria-hidden="true">
  <defs>
    <linearGradient id="redBand" x1="0" y1="0" x2="1" y2="1">
      <stop offset="0" stop-color="#c8102f"/><stop offset=".5" stop-color="#dc1d44"/><stop offset="1" stop-color="#b70d2e"/>
    </linearGradient>
    <linearGradient id="purpleBand" x1="0" y1="0" x2="1" y2="1">
      <stop offset="0" stop-color="#3c1673"/><stop offset=".5" stop-color="#5a2690"/><stop offset="1" stop-color="#34126a"/>
    </linearGradient>
  </defs>
  <rect x="0" y="500" width="1200" height="568" fill="url(#redBand)"/>
  <path d="M0 500 H1200 V520 Q600 700 0 520 Z" fill="#fff"/>
  <rect x="0" y="2427" width="1200" height="950" fill="var(--grey-band)"/>
  <path d="M0 2880 Q600 3080 1200 2880 V3377 H0 Z" fill="url(#purpleBand)"/>
</svg>

<!-- nav -->
<div class="abs brand" style="left:160px;top:42px">VELMORA<span class="dot"></span></div>
<nav>
  <span class="abs nav-link active" style="left:441px">Home</span>
  <span class="abs nav-link" style="left:507px">About us</span>
  <span class="abs nav-link" style="left:590px">KYC Product</span>
  <span class="abs nav-link" style="left:695px">Loyalty Product</span>
  <span class="abs nav-link" style="left:817px">Team</span>
  <span class="abs nav-link" style="left:879px">Contact us</span>
</nav>
<div class="abs login">LOGIN</div>

<!-- hero -->
<h1 class="abs hero-title"><span>Blockchain</span><br>solutions provider</h1>
<ul class="abs ticks">
  <li><svg viewBox="0 0 20 20"><circle cx="10" cy="10" r="10" fill="var(--red)"/><path d="M5.5 10.5l3 3 6-6.5" stroke="#fff" stroke-width="2.4" fill="none"/></svg>Solving problems that matter</li>
  <li><svg viewBox="0 0 20 20"><circle cx="10" cy="10" r="10" fill="var(--red)"/><path d="M5.5 10.5l3 3 6-6.5" stroke="#fff" stroke-width="2.4" fill="none"/></svg>Create a collaborative environment for all organisation</li>
</ul>
<div class="abs btn hero-btn">Contact us</div>
<div class="abs emblem"><span class="mark"></span><span class="name">Velmora</span></div>

<!-- why -->
<h2 class="abs why-title">Why Velmora?</h2>
<p class="abs why-text">Velmora Technology is a technology enabler that pledges to tackle issues that have plagued organisations for years. The company is lead by a team with tremendous expertise in the field of blockchain, mobile, IT, payment and financial sector. Being a global team, the company has influence in Singapore, China , France and more.</p>
<div class="abs video" role="img" aria-label="Teaser video still: hands typing on a laptop with a network of padlock icons"></div>
<div class="abs play"></div>
<svg class="abs" style="left:593px;top:1088px" width="20" height="22" aria-hidden="true"><path d="M2 1 L18 11 L2 21 Z" fill="#fff"/></svg>

<!-- products -->
<h2 class="abs section-title" style="top:1438px;color:var(--purple)">Our Products</h2>

<h3 class="abs prod-h" style="left:195px;top:1600px">KYC Product</h3>
<p class="abs prod-p" style="left:195px;top:1655px">It is a long established fact that a reader will be distracted by the readable content of a page when looking at its layout. The point of using Lorem Ipsum is that it has a more-or-less normal distribution of letters, as opposed to using 'Content here, content here', making it look like readable English. Many desktop publishing packages and web page editors now use</p>
<div class="abs disc" style="left:705px;top:1570px;width:280px;height:280px"></div>
<div class="abs ring" style="left:722px;top:1560px;width:300px;height:300px"></div>
<div class="abs art" style="left:770px;top:1655px;width:170px;height:240px;background:linear-gradient(160deg,#ffffff 0%,#f3f3f3 55%,#f04a5e 100%);box-shadow:0 6px 14px rgba(0,0,0,.15)" role="img" aria-label="Illustration of identity documents with a profile card for the KYC product"></div>

<div class="abs disc" style="left:225px;top:1975px;width:280px;height:280px"></div>
<div class="abs ring" style="left:180px;top:1962px;width:300px;height:300px"></div>
<div class="abs art" style="left:200px;top:2060px;width:300px;height:230px;background:linear-gradient(160deg,#f7f7f7 0%,#e4e6ea 55%,#3a3f4e 100%)" role="img" aria-label="Illustration of a person presenting a loyalty dashboard on a monitor"></div>
<h3 class="abs prod-h" style="left:562px;top:2030px">Loyalty Product</h3>
<p class="abs prod-p" style="left:562px;top:2085px">It is a long established fact that a reader will be distracted by the readable content of a page when looking at its layout. The point of using Lorem Ipsum is that it has a more-or-less normal distribution of letters, as opposed to using 'Content here, content here', making it look like readable English. Many desktop publishing packages and web page editors now use</p>

<!-- blog -->
<h2 class="abs section-title" style="top:2495px;color:var(--ink)">Latest Blog</h2>

<div class="abs card-img" style="left:156px;top:2600px;background:linear-gradient(135deg,#1e4f7d,#7fb0d6 50%,#2b5e8c)" role="img" aria-label="Blog photo: hands holding a phone with digital currency graphics"></div>
<div class="abs date" style="left:156px;top:2760px"><b>Dec 03</b><i></i></div>
<div class="abs card-t" style="left:156px;top:2792px">Neque porro quisquam dolorem</div>
<p class="abs card-p" style="left:156px;top:2818px">It has survived not only five centuries, but also the leap into electronic typesetting.</p>
<div class="abs card-more" style="left:156px;top:2862px">View More »</div>

<div class="abs card-img" style="left:459px;top:2600px;background:linear-gradient(135deg,#0f1f22,#8a7a2e 50%,#132528)" role="img" aria-label="Blog photo: glowing golden chain links on a dark background"></div>
<div class="abs date" style="left:459px;top:2760px"><b>Dec 03</b><i></i></div>
<div class="abs card-t" style="left:459px;top:2792px">Porro quisquam est qui</div>
<p class="abs card-p" style="left:459px;top:2818px">It has survived not only five centuries, but also the leap into electronic typesetting.</p>
<div class="abs card-more" style="left:459px;top:2862px">View More »</div>

<div class="abs card-img" style="left:766px;top:2600px;background:linear-gradient(135deg,#8a5a3c,#b8bcc4 45%,#5d6470)" role="img" aria-label="Blog photo: businessman in front of a digital network wall"></div>
<div class="abs date" style="left:766px;top:2760px"><b>Dec 03</b><i></i></div>
<div class="abs card-t" style="left:766px;top:2792px">Dolorem ipsum quia dolor</div>
<p class="abs card-p" style="left:766px;top:2818px">It has survived not only five centuries, but also the leap into electronic typesetting.</p>
<div class="abs card-more" style="left:766px;top:2862px">View More »</div>

<!-- join -->
<h2 class="abs join-h">Do you want to be part of our teams?</h2>
<p class="abs join-p">Neque porro quisquam est qui dolorem ipsum<br>quia dolor sit amet, consectetur,</p>
<div class="abs btn join-btn">Contact us</div>

<!-- footer -->
<div class="abs brand" style="left:160px;top:3505px">VELMORA<span class="dot"></span></div>
<div class="abs social" aria-label="Social links"><span></span><span class="r"></span><span></span><span></span></div>

<div class="abs f-h" style="left:462px;top:3472px">CONTACT US</div>
<svg class="abs" style="left:458px;top:3525px" width="16" height="20" aria-hidden="true"><path d="M8 1a6 6 0 0 1 6 6c0 5-6 12-6 12S2 12 2 7a6 6 0 0 1 6-6z" fill="none" stroke="var(--red)" stroke-width="1.6"/><circle cx="8" cy="7" r="2" fill="var(--red)"/></svg>
<div class="abs contact-item" style="left:486px;top:3520px"><b>Address</b>27 Harlow Lane Brightwater,<br>Northern Coast</div>
<svg class="abs" style="left:458px;top:3588px" width="18" height="18" aria-hidden="true"><path d="M4 1l3 4-2 2c1 2 3 4 5 5l2-2 4 3-2 3C8 16 2 10 1 4z" fill="none" stroke="var(--red)" stroke-width="1.5"/></svg>
<div class="abs contact-item" style="left:486px;top:3586px"><b>Phone number</b>04 21 76 30 58</div>

<div class="abs f-h" style="left:740px;top:3472px">ABOUT</div>
<ul class="abs f-list" style="left:740px;top:3518px"><li>Home</li><li>About Us</li><li>Services</li><li>Help us</li></ul>

<div class="abs f-h" style="left:937px;top:3472px">RESOURCES</div>
<ul class="abs f-list" style="left:937px;top:3518px"><li>Support</li><li>Why Us</li><li>Testimonials</li><li>FAQ</li></ul>

<div class="abs copy">© 2019 Company Name  All right reserved</div>

</body>
</html>
```